Baby Organic Coconut Body Lotion

Meadow Hush Naturals is developing a line of Organic and Natural skin care products for babies and toddlers, although our skin care can also be used by adults too. These products include a body lotion, shampoo & body wash, powder, hair cream, massage body oil, bath soak, baby balm, Bar Soap, gift box and many more.
This will be an ever expanding line so the list will go on and on. We are looking forward for an eye catching designs. I attached some of our current label designs and product images. Also, we have different Baby organic body lotion and Baby organic shampoo & body wash with different fruit flavours. Coconut lotion will share the same design with the shampoo & body wash. I would like you to start with the coconut design. I have uploaded plastic bottles with different colourful caps. The bottle with the white cap is for the coconut design. the bottle with the red cap is for the strawberry design. the bottle with the orange cap is for the orange design. the bottle with the yellow cap is for the pineapple design. the bottle with the green cap is for the apple design. Bear in my mind that my baby organic skin care are made with different fruit flavours.
Target Market(s)
My target market are for mothers that wants to buy there baby and toddler skin care products.
Industry/Entity Type
Baby
Look and feel

```html
<!DOCTYPE html>
<html lang="en">
<head>
<meta charset="utf-8">
<title>Meadow Hush Naturals – Pineapple Labels</title>
<link rel="stylesheet" href="https://fonts.googleapis.com/css2?family=Antonio:wght@100&family=Josefin+Sans:wght@300&family=Montserrat:wght@900&display=swap">
<style>
  :root {
    --ink: #000000;
    --paper: #ffffff;
    --sunshine: #fdd14a;
    --leaf: #1f8a3f;
  }
  html, body {
    margin: 0;
    padding: 0;
    width: 1200px;
    height: 1000px;
    overflow: hidden;
    background: var(--paper);
  }
  .label-sheet {
    display: block;
    width: 1200px;
    height: 1000px;
  }
  .brand-name {
    font-family: "Antonio", sans-serif;
    font-weight: 100;
    fill: var(--ink);
  }
  .flavour-name {
    font-family: "Montserrat", sans-serif;
    font-weight: 900;
    fill: var(--ink);
  }
  .product-type,
  .size-mark {
    font-family: "Josefin Sans", sans-serif;
    font-weight: 300;
    fill: var(--ink);
  }
  .badge-outline { fill: var(--paper); stroke: var(--ink); stroke-width: 8; stroke-linejoin: miter; }
  .badge-band { fill: none; stroke: var(--sunshine); stroke-width: 10; stroke-linejoin: miter; }
  .rule { stroke: var(--ink); stroke-width: 2.5; }
  .star { fill: var(--ink); }
</style>
</head>
<body>
<svg class="label-sheet" viewBox="0 0 1200 1000" xmlns="http://www.w3.org/2000/svg">
  <defs>
    <linearGradient id="fruit-tone" x1="0" y1="0" x2="0" y2="1">
      <stop offset="0" stop-color="#1f8a3f"/>
      <stop offset="0.3" stop-color="#1f8a3f"/>
      <stop offset="0.45" stop-color="#fdd14a"/>
      <stop offset="1" stop-color="#fdd14a"/>
    </linearGradient>
    <polygon id="star-shape" points="0,-15 4.4,-4.6 15,-4.6 6.5,2.2 9.3,13 0,6.4 -9.3,13 -6.5,2.2 -15,-4.6 -4.4,-4.6"/>
    <g id="badge-frame">
      <polygon class="badge-outline" points="337,477 512,577 512,778 337,878 163,778 163,577"/>
      <polygon class="badge-band" points="337,490 502,584 502,772 337,866 173,772 173,584"/>
      <use href="#star-shape" class="star" x="238" y="600"/>
      <use href="#star-shape" class="star" x="440" y="602"/>
      <line class="rule" x1="272" y1="628" x2="402" y2="628"/>
      <line class="rule" x1="193" y1="640" x2="482" y2="640"/>
      <line class="rule" x1="193" y1="709" x2="482" y2="709"/>
      <line class="rule" x1="272" y1="720" x2="402" y2="720"/>
      <rect role="img" aria-label="Pineapple illustration with green leafy crown"
            x="282" y="364" width="162" height="254" rx="40" fill="url(#fruit-tone)"/>
    </g>
  </defs>

  <!-- Body lotion label -->
  <g class="label label--lotion">
    <text class="brand-name" x="336" y="210" font-size="92" text-anchor="middle" textLength="305" lengthAdjust="spacingAndGlyphs">MEADOW</text>
    <text class="brand-name" x="336" y="268" font-size="50" text-anchor="middle">HUSH</text>
    <text class="brand-name" x="336" y="360" font-size="90" text-anchor="middle" textLength="350" lengthAdjust="spacingAndGlyphs">NATURALS</text>
    <use href="#badge-frame"/>
    <text class="flavour-name" x="337" y="697" font-size="60" text-anchor="middle" textLength="292" lengthAdjust="spacingAndGlyphs">PINEAPPLE</text>
    <text class="product-type" x="337" y="755" font-size="28" text-anchor="middle" letter-spacing="3">BODY</text>
    <text class="product-type" x="337" y="787" font-size="28" text-anchor="middle" letter-spacing="3">LOTION</text>
    <text class="size-mark" x="337" y="832" font-size="44" text-anchor="middle">T</text>
  </g>

  <!-- Shampoo + body wash label -->
  <g class="label label--wash" transform="translate(500 0)">
    <text class="brand-name" x="336" y="210" font-size="92" text-anchor="middle" textLength="305" lengthAdjust="spacingAndGlyphs">MEADOW</text>
    <text class="brand-name" x="336" y="268" font-size="50" text-anchor="middle">HUSH</text>
    <text class="brand-name" x="336" y="360" font-size="90" text-anchor="middle" textLength="350" lengthAdjust="spacingAndGlyphs">NATURALS</text>
    <use href="#badge-frame"/>
    <text class="flavour-name" x="337" y="697" font-size="60" text-anchor="middle" textLength="292" lengthAdjust="spacingAndGlyphs">PINEAPPLE</text>
    <text class="product-type" x="337" y="755" font-size="28" text-anchor="middle" textLength="290" lengthAdjust="spacing">SHAMPOO+BODY</text>
    <text class="product-type" x="337" y="787" font-size="28" text-anchor="middle" letter-spacing="3">WASH</text>
    <text class="size-mark" x="337" y="832" font-size="44" text-anchor="middle">T</text>
  </g>
</svg>
</body>
</html>
```